Property Finance Company - Orbin Funding Limited

Background: Orbin Funding Group Limited is a private property finance company. Orbin Funding Group has capital to directly fund first mortgage, mezzanine and preferred equity financing. We also acquire performing, sub-performing and distressed debt.

Orbin Fundings management philosophy emphasises expertise, innovation, wisdom, honesty and competitiveness. Orbin Funding are not finance brokers - we provide debt funding to the commercial property and residential development sectors. Our process is built from experience and cumutavely Orbin Fundings Directors have in excess of 60 years wisdom.

The aim of the website will be to increase brand awareness, provide clients with comfort around our level of skill and background on who we are, generate more sales, and provide examples of projects that we have funded.

The website is a new product launch, and we need to use our Orbin Funding logo that has just been designed. We like a dark background, and either black/silver/grey/ jade green, or black/gold/jade green colours.

Our unique advantages are that we have fast turnaround times, we can solve clients funding problems and we know what we are doing. Our target audience will be viewing the website on both desktop and mobile devices.

We would like to have the following pages:

Home
About
Team
Services
Project Experience
Contact

Competitors Website: http://www.tarvolo.example/

We would also like to have the option of video footage in our website, as you can see in our competitors website.

Overall we want a really slick, elegant but modern website that is better than www.tarvolo.example

Target Market(s)

Finance borrowers, property developers, accountants, lawyers, businesspeople, high net worth people

Industry/Entity Type

Finance

Requirements
Must have
• Please see project description
Nice to have
Should not have

```html
<!DOCTYPE html>
<html lang="en">
<head>
<meta charset="utf-8">
<title>Orbin Funding Group</title>
<link rel="stylesheet" href="https://fonts.googleapis.com/css2?family=Roboto:wght@400;500;700&family=Open+Sans:wght@400;600&display=swap">
<style>
  :root {
    --ink: #141414;
    --charcoal: #2b2b2b;
    --white: #ffffff;
    --muted: #e6e6e6;
    --jade-light: #14955a;
    --jade-dark: #0b5e2a;
    --grey-dark: #5a5a5c;
    --grey-light: #c9c9cb;
  }
  * { margin: 0; padding: 0; box-sizing: border-box; }
  html, body { width: 1200px; height: 2715px; overflow: hidden; background: var(--ink); }
  body { position: relative; font-family: "Open Sans", Arial, sans-serif; color: var(--white); }
  .abs { position: absolute; }
  h1, h2, h3 { font-family: "Roboto", Arial, sans-serif; font-weight: 400; }
  .btn {
    position: absolute; border: 2px solid var(--white); color: var(--white);
    font-family: "Roboto", Arial, sans-serif; font-size: 14px; letter-spacing: .5px;
    display: flex; align-items: center; justify-content: center; text-transform: uppercase;
  }

  /* Hero */
  .hero { position: absolute; left: 0; top: 0; width: 1200px; height: 673px;
    background: linear-gradient(180deg, #6a5a3c 0%, #4a4236 30%, #2e2c2a 65%, #1c1c1c 100%); }
  .brand { left: 120px; top: 44px; display: flex; align-items: center; gap: 14px; }
  .brand-mark { width: 56px; height: 56px; border-radius: 50%; background: var(--white); }
  .brand-name { font-family: "Roboto", Arial, sans-serif; font-size: 28px; font-weight: 500; line-height: 1; letter-spacing: 1px; }
  .menu-icon { left: 1029px; top: 56px; width: 32px; }
  .menu-icon span { display: block; height: 3px; background: var(--white); margin-bottom: 5px; }
  .play { left: 538px; top: 235px; }
  .hero-title { top: 385px; width: 1200px; text-align: center; font-size: 38px; letter-spacing: .5px; }
  .hero-sub { top: 438px; width: 1200px; text-align: center; font-size: 25px; font-family: "Roboto", Arial, sans-serif; }
  .chevron { left: 582px; top: 632px; }

  /* About */
  .about { position: absolute; left: 0; top: 673px; width: 1200px; height: 445px;
    background: linear-gradient(90deg, var(--grey-dark) 0%, #8c8c8e 45%, var(--grey-light) 100%); }
  .about h2 { left: 138px; top: 80px; font-size: 31px; }
  .about p { left: 136px; top: 136px; width: 520px; font-size: 14px; line-height: 28px; color: var(--muted); }
  .about .btn { left: 136px; top: 308px; width: 154px; height: 38px; }
  .about-emblem { left: 720px; top: 70px; width: 300px; height: 300px; border-radius: 50%;
    background: radial-gradient(circle, rgba(90,90,92,.35), rgba(90,90,92,.1)); }

  /* Services */
  .services { position: absolute; left: 0; top: 1118px; width: 1200px; height: 380px;
    background: linear-gradient(120deg, var(--jade-light) 0%, #11803f 50%, var(--jade-dark) 100%); }
  .services h2 { left: 152px; top: 80px; font-size: 30px; }
  .service { top: 160px; width: 300px; }
  .service h3 { font-size: 17px; font-weight: 500; margin-bottom: 14px; }
  .service p { font-size: 11px; line-height: 23px; color: var(--muted); height: 70px; }
  .service a { display: block; margin-top: 12px; font-family: "Roboto", Arial, sans-serif; font-size: 14px; color: var(--white); text-decoration: none; }

  /* Projects */
  .projects { position: absolute; left: 0; top: 1498px; width: 1200px; height: 557px; background: var(--ink); }
  .projects h2 { left: 158px; top: 45px; font-size: 28px; }
  .tile { position: absolute; }
  .tile-a { left: 157px; top: 107px; width: 283px; height: 177px; background: linear-gradient(135deg, #4a4a4a, #2a2a2a); }
  .tile-a .overlay { position: absolute; inset: 0; background: rgba(60,60,60,.55); padding: 55px 0 0 42px; }
  .tile-a h3 { font-size: 17px; font-weight: 500; margin-bottom: 4px; }
  .tile-a p { font-size: 11px; line-height: 17px; width: 210px; color: var(--muted); }
  .tile-b { left: 157px; top: 297px; width: 283px; height: 175px; background: linear-gradient(160deg, #b7c6d4, #6e7e8c 60%, #3b4752); }
  .tile-c { left: 451px; top: 107px; width: 597px; height: 365px; background: linear-gradient(200deg, #3f78a8 0%, #8fb0c4 35%, #d7b05a 65%, #5b4a2a 100%); }
  .projects .btn { left: 525px; top: 496px; width: 175px; height: 38px; font-size: 12px; }

  /* Experience */
  .experience { position: absolute; left: 0; top: 2055px; width: 1200px; height: 430px;
    background: linear-gradient(90deg, #3c3c3c 0%, #2a2a2a 100%); overflow: hidden; }
  .experience h2 { left: 152px; top: 103px; font-size: 28px; }
  .experience p { left: 152px; top: 145px; width: 520px; font-size: 15px; line-height: 28px; color: var(--muted); }
  .experience .btn { left: 158px; top: 283px; width: 153px; height: 40px; }
  .experience-photo { left: 575px; top: 30px; }

  /* Contact bar */
  .contact-bar { position: absolute; left: 0; top: 2485px; width: 1200px; height: 92px; background: var(--ink); }
  .contact-item { top: 36px; display: flex; align-items: center; gap: 10px; font-size: 14px; font-weight: 600; }

  /* Footer */
  .footer { position: absolute; left: 0; top: 2577px; width: 1200px; height: 138px; background: var(--charcoal); }
  .footer-nav { left: 146px; top: 34px; display: flex; gap: 20px; font-family: "Roboto", Arial, sans-serif; font-size: 12px; font-weight: 500; }
  .copyright { left: 150px; top: 68px; font-size: 12px; color: #bdbdbd; }
  .social { left: 914px; top: 28px; display: flex; gap: 8px; }
  .social span { width: 32px; height: 32px; border: 1.5px solid var(--white); border-radius: 50%; display: block; }
</style>
</head>
<body>

<header class="hero" role="img" aria-label="City skyline at sunset with video background">
  <div class="abs brand"><span class="brand-mark"></span><span class="brand-name">ORBIN FUNDING<br>GROUP</span></div>
  <div class="abs menu-icon"><span></span><span></span><span></span></div>
  <svg class="abs play" width="124" height="124" viewBox="0 0 124 124">
    <circle cx="62" cy="62" r="59" fill="none" stroke="#fff" stroke-width="4"/>
    <path d="M50 40 L82 62 L50 84 Z" fill="none" stroke="#fff" stroke-width="4" stroke-linejoin="round"/>
  </svg>
  <h1 class="abs hero-title">WELCOME TO ORBIN FUNDING GROUP</h1>
  <div class="abs hero-sub">MORBI DIAM MAURIS VIVERRA IN GRAVIDA</div>
  <svg class="abs chevron" width="36" height="18" viewBox="0 0 36 18"><path d="M1 1 L18 16 L35 1" fill="none" stroke="#fff" stroke-width="2"/></svg>
</header>

<section class="about">
  <h2 class="abs">ABOUT US</h2>
  <p class="abs">Orbin Funding Group Limited is a private property finance company. Orbin Funding Group has capital to directly fund first mortgage, mezzanine and preferred equity financing. We also acquire performing, sub-performing and distressed debt. Orbin Fundings management philosophy emphasises expertise, innovation, wisdom, honesty and competitiveness.</p>
  <div class="btn">Read More</div>
  <div class="abs about-emblem" role="img" aria-label="Faint brand emblem decoration"></div>
</section>

<section class="services">
  <h2 class="abs">OUR SERVICES</h2>
  <div class="abs service" style="left:157px">
    <h3>PROPERTY FINANCE</h3>
    <p>Morbi diam mauris viverra in gravida eu mattis in ante Morbi eget arcu Morbi porta libero id ullamcorper nonummy nibh ligula</p>
    <a href="#">READ MORE</a>
  </div>
  <div class="abs service" style="left:477px">
    <h3>DEBT FUNDING</h3>
    <p>Morbi diam mauris viverra in gravida eu mattis in ante Morbi eget arcu Morbi porta libero id ullamcorper nonummy nibh ligula</p>
    <a href="#">READ MORE</a>
  </div>
  <div class="abs service" style="left:798px">
    <h3>DIRECTLY FUND FIRST MORTGAGE</h3>
    <p>Morbi diam mauris viverra in gravida eu mattis in ante Morbi eget arcu Morbi porta libero id ullamcorper nonummy nibh ligula</p>
    <a href="#">READ MORE</a>
  </div>
</section>

<section class="projects">
  <h2 class="abs">OUR PROJECTS</h2>
  <div class="tile tile-a" role="img" aria-label="Office tower facade">
    <div class="overlay">
      <h3>PROJECT TITLE</h3>
      <p>Morbi diam mauris viverra in gravida eu mattis in ante Morbi eget arcu Morb</p>
    </div>
  </div>
  <div class="tile tile-b" role="img" aria-label="Glass towers viewed from below"></div>
  <div class="tile tile-c" role="img" aria-label="Apartment buildings under a sunny sky"></div>
  <div class="btn">View More Projects</div>
</section>

<section class="experience">
  <h2 class="abs">PROJECT EXPERIENCE</h2>
  <p class="abs">Vivamus porttitor purus nisi eleifend libero a tempus libero lectus feugiat felis Morbi diam mauris viverra in gravida eu mattis in ante Morbi eget arcu Morbi porta libero id ullamcorper nonummy nibh ligula pulvinar metus eget consectetuer augue nisi quis lacus</p>
  <div class="btn">Read More</div>
  <svg class="abs experience-photo" width="625" height="400" viewBox="0 0 625 400" role="img" aria-label="Black and white modern apartment building">
    <defs>
      <linearGradient id="buildingTone" x1="0" y1="0" x2="1" y2="1">
        <stop offset="0" stop-color="#e8e8e8"/>
        <stop offset="1" stop-color="#6e6e6e"/>
      </linearGradient>
    </defs>
    <polygon points="0,400 10,330 420,0 625,90 625,400" fill="url(#buildingTone)"/>
  </svg>
</section>

<section class="contact-bar">
  <div class="abs contact-item" style="left:157px">
    <svg width="14" height="20" viewBox="0 0 14 20"><path d="M7 0a7 7 0 0 0-7 7c0 5 7 13 7 13s7-8 7-13a7 7 0 0 0-7-7zm0 10a3 3 0 1 1 0-6 3 3 0 0 1 0 6z" fill="#fff"/></svg>
    48 Halden Row Suite 3 Marlow 20417
  </div>
  <div class="abs contact-item" style="left:565px">
    <svg width="20" height="20" viewBox="0 0 20 20"><path d="M4 1l4 4-2 3c1 2 3 4 5 5l3-2 4 4-3 3C8 18 2 12 1 4z" fill="none" stroke="#fff" stroke-width="1.5" stroke-linejoin="round"/></svg>
    555.014.7720
  </div>
  <div class="abs contact-item" style="left:828px">
    <svg width="20" height="14" viewBox="0 0 20 14"><rect x="1" y="1" width="18" height="12" fill="none" stroke="#fff" stroke-width="1.5"/><path d="M1 1l9 7 9-7" fill="none" stroke="#fff" stroke-width="1.5"/></svg>
    hello@orbinfunding.example
  </div>
</section>

<footer class="footer">
  <nav class="abs footer-nav"><span>HOME</span><span>ABOUT</span><span>TEAM</span><span>SERVICES</span><span>PROJECT EXPERIENCE</span><span>CONTACT</span></nav>
  <div class="abs copyright">© 2017 Company Name &nbsp;All right reserved</div>
  <div class="abs social"><span></span><span></span><span></span><span></span></div>
</footer>

</body>
</html>
```